Governance Research Alumni Fellows' Association Annual Symposium Poster

We need a poster to advertise for our annual symposium. The poster will be printed on 11X17" paper.

Our organization is the Governance Research Alumni Fellows' Association. Our logo is in the uploaded files.

The title of this year's symposium is "Lakeside Currents - Paths Beyond Borders." The Symposium will take place on March 31, 2017 in HL - 41.

We are accepting papers on the topics of Canada and the world; Indigenous politics in Canada; Canadian national identity; Race, racialization and belonging; Gender and politics in Canada; Queer politics and sexualities; Class and labour politics in Canada; Environmental politics; Canadian government and politics.

There will be a lunch hour roundtable discussion on the topic of "Unweaving the Threads of Civic Inquiry."
Confirmed Speakers include Dr. Rosalind Okafor, Dr. Teresa Valdomero-Cuesta, Dr. Owen Tillard, Dr. Harriet Brisco
This round-table will consider questions of Race, Indigeneity, and Ethnicity in Political Science Research and efforts by the universities to "Decolonize," "Indigenize," and "Reconcile" the academy.
The roundtable will take place in HL-41 from 12:00 - 1:00 pm.
Lunch will be provided.

There will be a keynote panel sponsored by the Northern Institute for Civilian Safeguard Studies on the topic of "Canada’s renewed vision of peacekeeping."
Their logo is in the uploaded files.

For more information and a full schedule or events, visit our website: http://grafaforum.quillpage.example/credits.html

Sponsors should be listed at the bottom of the page: The Faculty of Arts, The Department of Political Science, NICSS

Target Market(s)

University students and staff who may come to the symposium

Industry/Entity Type

Political

Logo Text

GRAFA Governance Research Alumni Fellows' Association

Font styles to use
Sans Serif

Colors
ec1f27
f37122
9bcb3c
ffcf3e

Requirements
Must have
• Coulours/Leaves/etc should match this website:
• http://grafaforum.quillpage.example/credits.html
• Title of Symposium, Date, Room Number
• Sponsor logos at the bottom of the page
• Date/Time for Roundtable
Nice to have
• This list:
• We are accepting papers on the topics of Canada and the world; Indigenous politics in Canada; Canadian national identity; Race, racialization and belonging; Gender and politics in Canada; Queer politics and sexualities; Class and labour politics in Canada; Environmental politics; Canadian government and politics.
• This statement:
• This round-table will consider questions of Race, Indigeneity, and Ethnicity in Political Science Research and efforts by the universities to "Decolonize," "Indigenize," and "Reconcile" the academy.

```html
<!DOCTYPE html>
<html lang="en">
<head>
<meta charset="utf-8">
<title>GRAFA Symposium 2017 – Lakeside Currents</title>
<link rel="stylesheet" href="https://fonts.googleapis.com/css2?family=Raleway:wght@300;400;500;600;700;800&family=Yellowtail&display=swap">
<style>
  :root {
    --red: #ec1f27;
    --deep-red: #a21d22;
    --orange: #f37122;
    --green: #9bcb3c;
    --yellow: #ffcf3e;
    --gold: #f6c434;
    --ink: #1f1f1f;
    --black: #141414;
    --mist: #e6e6e6;
    --mist-light: #ebebeb;
    --white: #ffffff;
    --forest: #1f7a3a;
    --logo-blue: #2b7fc1;
    --link-red: #b5242a;
  }
  * { margin: 0; padding: 0; box-sizing: border-box; }
  html, body { width: 776px; height: 1200px; overflow: hidden; background: var(--white); }
  body { font-family: "Raleway", Arial, sans-serif; color: var(--ink); }

  .poster { position: relative; width: 776px; height: 1200px; overflow: hidden; }

  /* Hero */
  .hero { position: absolute; left: 0; top: 0; width: 776px; height: 453px; }
  .hero-art {
    position: absolute; inset: 0;
    background:
      linear-gradient(90deg, #9fae3a 0%, #c8b73c 30%, #d6962e 55%, #c9462a 80%, #b8262a 100%) top / 100% 42px no-repeat,
      linear-gradient(90deg, #b3b43a 0%, #cfbf3d 35%, #c7862c 60%, #c23a2a 85%, #b21f26 100%) bottom / 100% 30px no-repeat,
      radial-gradient(ellipse 230px 170px at 150px 250px, rgba(214,52,32,.95), rgba(214,52,32,0) 100%),
      radial-gradient(ellipse 300px 200px at 470px 230px, rgba(196,120,44,.85), rgba(196,120,44,0) 100%),
      radial-gradient(ellipse 200px 160px at 640px 280px, rgba(170,60,40,.7), rgba(170,60,40,0) 100%),
      linear-gradient(180deg, #3a3533 0%, #2b2826 50%, #34302d 100%);
  }
  .hero-date {
    position: absolute; top: 27px; left: 0; width: 100%;
    text-align: center; color: var(--white);
    font-weight: 800; font-size: 24.5px; letter-spacing: .2px;
  }
  .org-mark {
    position: absolute; top: 212px; left: 0; width: 100%;
    text-align: center; color: var(--logo-blue); font-weight: 800;
  }
  .org-mark .org-short { display: block; font-size: 74px; line-height: 70px; letter-spacing: -1px; }
  .org-mark .org-long { display: block; font-size: 15.5px; margin-top: 8px; letter-spacing: .3px; }

  /* Title band */
  .title-band {
    position: absolute; top: 453px; left: 0; width: 776px; height: 112px;
    background: var(--black); color: var(--white);
  }
  .title-band .presents {
    position: absolute; left: 122px; top: 20px;
    font-family: "Yellowtail", cursive; color: var(--gold); font-size: 31px;
  }
  .title-band .title-main {
    position: absolute; left: 234px; top: 18px;
    color: var(--gold); font-weight: 500; font-size: 36px; letter-spacing: 1px;
  }
  .title-band .title-sub {
    position: absolute; left: 148px; top: 63px;
    color: #e8e8e8; font-weight: 300; font-size: 33px; letter-spacing: 2.5px;
  }

  /* Topics */
  .topics {
    position: absolute; top: 565px; left: 0; width: 776px; height: 210px;
    background: var(--mist);
  }
  .topics h2 {
    position: absolute; top: 16px; width: 100%; text-align: center;
    font-weight: 700; font-size: 20.5px; color: var(--ink);
  }
  .topic-list { position: absolute; top: 38px; list-style: none; font-size: 17px; line-height: 25.5px; color: #2a2a2a; }
  .topic-list li::before { content: "• "; font-size: 12px; vertical-align: 2px; }
  .topic-list.left { left: 66px; }
  .topic-list.right { left: 400px; }

  /* Roundtable */
  .roundtable {
    position: absolute; top: 775px; left: 0; width: 776px; height: 155px;
    background: var(--deep-red); text-align: center; color: var(--white);
  }
  .roundtable h2 { position: absolute; top: 20px; width: 100%; font-size: 16.5px; font-weight: 700; color: var(--gold); }
  .roundtable .speakers { position: absolute; top: 47px; width: 100%; font-size: 12.5px; font-weight: 500; letter-spacing: .4px; }
  .roundtable .when { position: absolute; top: 77px; width: 100%; font-size: 15px; font-weight: 400; color: var(--orange); }
  .roundtable .when strong { font-weight: 700; color: var(--gold); }
  .roundtable .about { position: absolute; top: 97px; width: 100%; font-size: 13.5px; line-height: 17px; }

  /* Keynote */
  .keynote {
    position: absolute; top: 930px; left: 0; width: 776px; height: 160px;
    background: var(--mist-light); text-align: center;
  }
  .keynote .label { position: absolute; top: 20px; width: 100%; font-size: 14.5px; font-weight: 700; }
  .keynote h2 { position: absolute; top: 39px; width: 100%; font-size: 20px; font-weight: 400; letter-spacing: .4px; }
  .keynote .sponsor-note { position: absolute; top: 64px; width: 100%; font-size: 16px; font-weight: 700; }
  .keynote .more { position: absolute; top: 99px; width: 100%; font-size: 16px; font-weight: 700; color: var(--link-red); }
  .keynote .url { position: absolute; top: 116px; width: 100%; font-size: 17px; font-weight: 500; color: var(--ink); }

  /* Sponsors */
  .sponsors { position: absolute; top: 1090px; left: 0; width: 776px; height: 110px; background: var(--white); }
  .sponsor { position: absolute; top: 30px; display: flex; align-items: center; gap: 8px; }
  .sponsor .mark { flex: none; }
  .sponsor.institute { left: 42px; top: 30px; color: var(--ink); font-size: 28px; font-weight: 700; }
  .sponsor.faculty { left: 210px; color: var(--forest); font-size: 16px; line-height: 19px; font-weight: 700; }
  .sponsor.department { left: 470px; color: var(--forest); font-size: 13px; line-height: 15px; font-weight: 700; }
  .sponsor.council { left: 684px; color: var(--forest); font-size: 13px; line-height: 15px; font-weight: 700; }
</style>
</head>
<body>
<main class="poster">

  <header class="hero">
    <div class="hero-art" role="img" aria-label="Collage of smiling student portraits over dark asphalt with a large red autumn maple leaf, framed by green, yellow, orange and red leaf bands"></div>
    <p class="hero-date">FRIDAY MARCH 31, 2017 9:00AM-5:00PM IN HL - 41</p>
    <div class="org-mark">
      <span class="org-short">GRAFA</span>
      <span class="org-long">GOVERNANCE RESEARCH ALUMNI FELLOWS' ASSOCIATION</span>
    </div>
  </header>

  <section class="title-band">
    <span class="presents">presents:</span>
    <h1>
      <span class="title-main">LAKESIDE CURRENTS</span>
      <span class="title-sub">PATHS BEYOND BORDERS.</span>
    </h1>
  </section>

  <section class="topics">
    <h2>Student Panel Discussions will consider topics such as:</h2>
    <ul class="topic-list left">
      <li>Canada and the world;</li>
      <li>Indigenous politics in Canada;</li>
      <li>Canadian national identity;</li>
      <li>Race, racialization and belonging;</li>
      <li>Gender and politics in Canada;</li>
    </ul>
    <ul class="topic-list right">
      <li>Queer politics and sexualities;</li>
      <li>Class and labour politics in Canada;</li>
      <li>Environmental politics; or</li>
      <li>Canadian government and politics.</li>
    </ul>
  </section>

  <section class="roundtable">
    <h2>Lunchtime Roundtable, "Unweaving the Threads of Civic Inquiry," Featuring</h2>
    <p class="speakers">DR. ROSALIND OKAFOR &bull; DR. TERESA VALDOMERO-CUESTA &bull; DR. OWEN TILLARD &bull; DR. HARRIET BRISCO</p>
    <p class="when"><strong>FRIDAY MARCH 31, 2017 12:00-1:00PM IN HL - 41 -</strong> LUNCH WILL BE PROVIDED.</p>
    <p class="about">This round-table will consider questions of Race, Indigeneity, and Ethnicity in Political Science<br>research and efforts by universities to "Decolonize," "Indigenize," and "Reconcile" the academy.</p>
  </section>

  <section class="keynote">
    <p class="label">Keynote Panel:</p>
    <h2>“CANADA'S RENEWED VISION OF PEACEKEEPING"</h2>
    <p class="sponsor-note">This panel is sponsored by the Northern Institute for Civilian Safeguard Studies</p>
    <p class="more">For more information and a full schedule or events, visit our website:</p>
    <p class="url">grafaforum.quillpage.example/credits.html</p>
  </section>

  <footer class="sponsors">
    <div class="sponsor institute">
      <span>NICSS</span>
    </div>
    <div class="sponsor faculty">
      <svg class="mark" width="28" height="32" viewBox="0 0 28 32" aria-hidden="true"><rect width="28" height="32" fill="var(--forest)"/></svg>
      <span>NORTHGATE UNIVERSITY<br>FACULTY OF ARTS</span>
    </div>
    <div class="sponsor department">
      <svg class="mark" width="26" height="30" viewBox="0 0 26 30" aria-hidden="true"><rect width="26" height="30" fill="var(--forest)"/></svg>
      <span>NORTHGATE UNIVERSITY<br>FACULTY OF ARTS<br>Department of Political Science</span>
    </div>
    <div class="sponsor council">
      <span>GRADUATE<br>COUNCIL</span>
    </div>
  </footer>

</main>
</body>
</html>
```